Allied Health team of Physiotherapists & Occupational Therapists seek a business card design

We have our new logo, we now need our new business cards and stationary. Tidewell: Oedema & Family Clinic is seeking a generic card design to represent our whole team and individual cards for each therapist that incorporates our new logo to communicate our holistic approach that is calming, nuturing, supportive and welcoming.
Our Physiotherapists and Occupational Therapists assess, treat and provide education for people who are at risk of or who have lymphoedema. This is often as a result of treatment for cancer. We provide pre-operative and post-operative management and cancer rehabilitation in our Pilates studio. Our team also consists of Physiotherapists who have a strong interest in pelvic floor and continence management for both men and women.

Target Market(s)

Mainly women health conscious

Industry/Entity Type

Allied Health: Physiotherapy / Occupational Therapy

Contact Information for Business Card

Address: 14 Gallivant Ave Frankston 3199 Phone: 84316570 fax: 8431 6578 Email: info@tidewellcareservices.com.au Website: tidewellcareservices.com.au Facebook address: facebook.com/TidewellOedemaAndFamilyCareClinic. Room to write appointments. Individual cards need to have name, office email and individual email and professional details

Requirements
Must have
• Logo as per uploaded documents

```html
<!DOCTYPE html>
<html lang="en">
<head>
<meta charset="utf-8">
<title>Tidewell: Oedema &amp; Family Clinic — Business Card</title>
<link href="https://fonts.googleapis.com/css2?family=Arimo:wght@400&family=Michroma&display=swap" rel="stylesheet">
<style>
  :root {
    --page: #ecebe8;
    --peach: #f7b088;
    --sage: #c5cdc6;
    --white: #ffffff;
    --ink: #2b2b2b;
    --ink-soft: #555555;
  }
  * { margin: 0; padding: 0; box-sizing: border-box; }
  html, body { width: 1200px; height: 900px; overflow: hidden; background: var(--page); }
  .canvas { position: relative; width: 1200px; height: 900px; }

  .card {
    position: absolute; width: 640px; height: 366px; overflow: hidden;
    box-shadow: 0 6px 18px rgba(0,0,0,0.12);
  }
  .card--back { left: 280px; top: 48px; background: var(--peach); }
  .card--front { left: 280px; top: 480px; background: var(--white); }

  .brand {
    position: absolute; display: flex; align-items: center; gap: 12px;
    font-family: "Arimo", sans-serif; font-weight: 400; font-size: 21px; line-height: 1.25;
  }
  .brand__dot { width: 18px; height: 18px; border-radius: 50%; flex: none; }
  .card--back .brand { left: 300px; top: 150px; width: 300px; color: var(--white); }
  .card--back .brand__dot { background: var(--white); }
  .card--front .brand { right: 36px; top: 74px; width: 220px; font-size: 17px; color: var(--peach); }
  .card--front .brand__dot { background: var(--peach); }

  .wave { position: absolute; left: 0; top: 0; width: 640px; height: 366px; }

  .person { position: absolute; left: 64px; top: 108px; }
  .person__name {
    font-family: "Michroma", sans-serif; font-size: 15px; letter-spacing: 2px; color: var(--ink);
  }
  .person__role {
    font-family: "Arimo", sans-serif; font-size: 8px; color: var(--ink-soft); margin-top: 2px;
  }

  .contacts { position: absolute; left: 80px; top: 164px; list-style: none; }
  .contacts li {
    display: flex; align-items: center; gap: 12px; height: 24px;
    font-family: "Arimo", sans-serif; font-size: 15px; color: var(--ink);
  }
  .contacts svg { width: 16px; height: 16px; flex: none; fill: var(--ink); }

  .address {
    position: absolute; right: 40px; top: 246px; text-align: right;
    font-family: "Arimo", sans-serif; font-size: 17px; line-height: 1.35; color: var(--white);
  }
</style>
</head>
<body>
<main class="canvas">

  <section class="card card--back" aria-label="Card back">
    <div class="brand"><span class="brand__dot"></span><span class="brand__name">Tidewell: Oedema &amp; Family Clinic</span></div>
  </section>

  <section class="card card--front" aria-label="Card front">
    <svg class="wave" viewBox="0 0 640 366" aria-hidden="true">
      <path d="M0 320 C190 326 360 292 480 214 C540 176 595 156 640 150 L640 366 L0 366 Z" fill="var(--peach)"/>
      <path d="M0 298 C190 306 350 274 468 202 L476 208 C356 284 190 314 0 314 Z" fill="var(--sage)"/>
    </svg>

    <div class="brand"><span class="brand__dot"></span><span class="brand__name">Tidewell: Oedema &amp; Family Clinic</span></div>

    <div class="person">
      <p class="person__name">ELLIS HARROW</p>
      <p class="person__role">CEO/Managing Director</p>
    </div>

    <ul class="contacts">
      <li>
        <svg viewBox="0 0 24 24"><path d="M6.6 10.8a15 15 0 0 0 6.6 6.6l2.2-2.2a1 1 0 0 1 1-.25 11.4 11.4 0 0 0 3.6.57 1 1 0 0 1 1 1V20a1 1 0 0 1-1 1A17 17 0 0 1 3 4a1 1 0 0 1 1-1h3.5a1 1 0 0 1 1 1c0 1.25.2 2.45.57 3.6a1 1 0 0 1-.25 1z"/></svg>
        <span>123 456 7890</span>
      </li>
      <li>
        <svg viewBox="0 0 24 24"><path d="M8 1h8a2 2 0 0 1 2 2v18a2 2 0 0 1-2 2H8a2 2 0 0 1-2-2V3a2 2 0 0 1 2-2zm0 3v14h8V4zm4 15.2a1 1 0 1 0 0 2 1 1 0 0 0 0-2z"/></svg>
        <span>123 465 7890</span>
      </li>
      <li>
        <svg viewBox="0 0 24 24"><path d="M2 5h20v14H2zm2 2v.4l8 5.4 8-5.4V7zm0 2.8V17h16V9.8l-8 5.4z"/></svg>
        <span>hello@tidewellmail.com</span>
      </li>
      <li>
        <svg viewBox="0 0 24 24"><path d="M12 2a10 10 0 1 0 0 20 10 10 0 0 0 0-20zm7.9 9h-3.4a15 15 0 0 0-1.3-6 8 8 0 0 1 4.7 6zM12 4c.9 1.3 2.2 3.8 2.5 7h-5C9.8 7.8 11.1 5.3 12 4zM8.8 5a15 15 0 0 0-1.3 6H4.1a8 8 0 0 1 4.7-6zM4.1 13h3.4a15 15 0 0 0 1.3 6 8 8 0 0 1-4.7-6zM12 20c-.9-1.3-2.2-3.8-2.5-7h5c-.3 3.2-1.6 5.7-2.5 7zm3.2-1a15 15 0 0 0 1.3-6h3.4a8 8 0 0 1-4.7 6z"/></svg>
        <span>www.tidewellcareservices.com.au</span>
      </li>
    </ul>

    <p class="address">1230 Brindlecombe<br>Dr Ashgrove, VA, US</p>
  </section>

</main>
</body>
</html>
```